Heron Loan Partners Business Card

We need a business card design for our mortgage servicing company. In addition to servicing the loans of homeowners, we help homeowners with purchasing their homes and any mortgage refinancing. We would like to see designs that use the colors in the logo attached below (gold-ish yellow and navy blue), and any other design you deem fit! The design should communicate a simpler life with smart mortgages provided by Heron.

```html
<!DOCTYPE html>
<html lang="en">
<head>
<meta charset="utf-8">
<title>Heron Loan Partners Business Card</title>
<link rel="stylesheet" href="https://fonts.googleapis.com/css2?family=EB+Garamond:wght@700&family=Montserrat:wght@400;500&display=swap">
<style>
  :root {
    --navy: #272154;
    --navy-deep: #1d1a4e;
    --gold: #e0b13c;
    --paper: #ffffff;
    --ink: #2a2650;
    --backdrop: #232323;
  }
  * { margin: 0; padding: 0; box-sizing: border-box; }
  html, body { width: 900px; height: 1200px; overflow: hidden; background: var(--backdrop); }
  .canvas { position: relative; width: 900px; height: 1200px; }
  .card { position: absolute; left: 136px; width: 630px; height: 360px; }
  .card-front { top: 213px; background: var(--navy); }
  .card-back { top: 627px; background: var(--paper); }

  .brand-name {
    font-family: "EB Garamond", Georgia, serif;
    font-weight: 700;
    color: var(--gold);
    white-space: nowrap;
    display: flex;
    align-items: center;
  }
  .brand-mark {
    display: inline-block;
    border-radius: 50%;
    background: var(--gold);
  }
  .card-front .brand-name {
    position: absolute; left: 0; right: 0; top: 152px;
    justify-content: center; gap: 14px;
    font-size: 50px; line-height: 1;
  }
  .card-front .brand-mark { width: 16px; height: 16px; }
  .card-back .brand-name {
    position: absolute; right: 38px; top: 66px;
    gap: 10px; font-size: 31px; line-height: 1;
  }
  .card-back .brand-mark { width: 11px; height: 11px; }

  .accent-bar { position: absolute; left: 0; top: 152px; width: 12px; height: 44px; background: var(--navy-deep); }
  .holder { position: absolute; left: 37px; top: 150px; }
  .holder-name {
    font-family: "EB Garamond", Georgia, serif; font-weight: 700;
    font-size: 23px; color: var(--gold); line-height: 1.1;
  }
  .holder-role {
    font-family: "Montserrat", Arial, sans-serif; font-size: 14.5px;
    color: var(--ink); letter-spacing: 0.6px; margin-top: 4px;
  }

  .contact {
    position: absolute; left: 379px; top: 200px;
    font-family: "Montserrat", Arial, sans-serif; color: var(--ink);
    font-size: 14.5px; letter-spacing: 0.6px;
  }
  .address p { line-height: 23px; }
  .contact-list { list-style: none; margin-top: 10px; }
  .contact-list li { display: flex; align-items: center; height: 24px; }
  .contact-list svg { width: 12px; height: 12px; margin-right: 7px; fill: var(--gold); flex: none; }
  .contact-phone { letter-spacing: 2.4px; }
</style>
</head>
<body>
<main class="canvas">
  <section class="card card-front" aria-label="Card front">
    <div class="brand-name"><span class="brand-mark"></span>Heron Loan Partners</div>
  </section>

  <section class="card card-back" aria-label="Card back">
    <div class="brand-name"><span class="brand-mark"></span>Heron Loan Partners</div>
    <span class="accent-bar"></span>
    <div class="holder">
      <p class="holder-name">Dana Whitford</p>
      <p class="holder-role">Founder</p>
    </div>
    <div class="contact">
      <div class="address">
        <p>418 Harbor Ave S</p>
        <p>Bayview, FL 33790</p>
      </div>
      <ul class="contact-list">
        <li class="contact-phone">
          <svg viewBox="0 0 24 24" aria-hidden="true"><path d="M6.6 10.8c1.4 2.8 3.8 5.1 6.6 6.6l2.2-2.2c.3-.3.7-.4 1-.2 1.1.4 2.3.6 3.6.6.6 0 1 .4 1 1V20c0 .6-.4 1-1 1C10.6 21 3 13.4 3 4c0-.6.4-1 1-1h3.5c.6 0 1 .4 1 1 0 1.3.2 2.5.6 3.6.1.3 0 .7-.2 1z"/></svg>
          (888)-555-0142
        </li>
        <li>
          <svg viewBox="0 0 24 24" aria-hidden="true"><path d="M2 5h20v14H2z M2 5l10 8 10-8" stroke="#fff" stroke-width="1.6"/></svg>
          info@heronloan.com
        </li>
        <li>
          <svg viewBox="0 0 24 24" aria-hidden="true"><circle cx="12" cy="12" r="10"/><path d="M2 12h20M12 2c3 3 3 17 0 20M12 2c-3 3-3 17 0 20" stroke="#fff" stroke-width="1.4" fill="none"/></svg>
          www.heronloan.com
        </li>
      </ul>
    </div>
  </section>
</main>
</body>
</html>
```